TalkHarbor - Language Coaching Services

Sleek, innovative, trendy design for Language Coaching business.

TalkHarbor is a new UK based company that provides Language Coaching services. We offer highly personalized on-line and face to face language courses. We also impart learning techniques workshops based on the latest neuroscience research for second-language acquisition.

Target Market(s)

See attached info

Industry/Entity Type

Consulting

Contact Information for Business Card

TalkHarbor
DaniaKV@talkharbor.co.uk
TalkHarbor.co.uk
London, UK

Font styles to use
Sans Serif

```html
<!DOCTYPE html>
<html lang="en">
<head>
<meta charset="utf-8">
<title>TalkHarbor Business Card</title>
<link rel="stylesheet" href="https://fonts.googleapis.com/css2?family=Lato:wght@400;700;900&display=swap">
<style>
  :root {
    --stage: #2e2f31;
    --card: #ffffff;
    --card-shade: #e9ecee;
    --brand: #1f6f93;
    --brand-deep: #17587a;
    --brand-faint: #c7dbe5;
    --ink: #33495a;
  }
  * { box-sizing: border-box; margin: 0; padding: 0; }
  html, body {
    width: 1200px;
    height: 997px;
    overflow: hidden;
    background: var(--stage);
    font-family: "Lato", Arial, sans-serif;
  }
  .stage {
    position: relative;
    width: 1200px;
    height: 997px;
  }
  .card {
    position: absolute;
    top: 355px;
    width: 520px;
    height: 298px;
    border-radius: 18px;
    background: linear-gradient(135deg, var(--card) 0%, var(--card) 55%, var(--card-shade) 100%);
    box-shadow: 0 18px 40px rgba(0,0,0,0.45);
    overflow: hidden;
  }
  .card--back { left: 50px; }
  .card--front { left: 630px; }

  /* back side */
  .back-ring {
    position: absolute;
    left: 150px;
    top: 20px;
    width: 260px;
    height: 260px;
    border-radius: 50%;
    border: 22px solid var(--brand-faint);
    opacity: 0.55;
  }
  .back-name {
    position: absolute;
    left: 0;
    right: 0;
    top: 62px;
    text-align: center;
    font-size: 54px;
    font-weight: 700;
    letter-spacing: 2px;
    color: var(--brand-faint);
  }
  .back-pitch {
    position: absolute;
    left: 0;
    right: 0;
    top: 150px;
    text-align: center;
    font-size: 12.5px;
    font-weight: 700;
    line-height: 1.6;
    color: var(--brand);
  }

  /* front side */
  .brand-block {
    position: absolute;
    left: 28px;
    top: 70px;
    width: 230px;
    text-align: center;
  }
  .brand-mark {
    width: 92px;
    height: 92px;
    margin: 0 auto 18px;
    border-radius: 50%;
    border: 6px solid var(--brand);
  }
  .brand-name {
    font-size: 34px;
    font-weight: 700;
    color: var(--brand);
    letter-spacing: 0.5px;
  }
  .divider {
    position: absolute;
    left: 285px;
    top: 40px;
    width: 2px;
    height: 200px;
    background: linear-gradient(to bottom, rgba(31,111,147,0), var(--brand-deep) 45%, rgba(31,111,147,0));
  }
  .contact {
    position: absolute;
    left: 305px;
    top: 40px;
    width: 205px;
    color: var(--ink);
  }
  .contact-name {
    font-size: 16px;
    font-weight: 400;
    color: var(--brand);
    text-transform: uppercase;
    letter-spacing: 0.5px;
    line-height: 1;
  }
  .contact-name strong { font-weight: 900; }
  .contact-role {
    font-size: 10.5px;
    color: var(--ink);
    margin-bottom: 14px;
  }
  .contact-address {
    font-size: 11.5px;
    font-weight: 700;
    line-height: 1.4;
    color: var(--brand-deep);
    margin-bottom: 18px;
  }
  .contact-list { list-style: none; }
  .contact-list li {
    display: flex;
    align-items: center;
    gap: 10px;
    font-size: 11.5px;
    line-height: 1;
    margin-bottom: 10px;
    color: var(--ink);
  }
  .contact-icon {
    width: 13px;
    height: 13px;
    flex: none;
    fill: var(--brand-deep);
  }
  .contact-dot {
    width: 11px;
    height: 11px;
    margin: 0 1px;
    flex: none;
    border-radius: 50%;
    background: var(--brand-deep);
  }
</style>
</head>
<body>
<main class="stage">

  <section class="card card--back" aria-label="Business card, back side">
    <div class="back-ring"></div>
    <div class="back-name">TalkHarbor</div>
    <p class="back-pitch">
      We offer<br>
      highly personalized on-line and face to face language courses.<br>
      We also impart learning techniques workshops based on the<br>
      latest neuroscience research for second-language acquisition.
    </p>
  </section>

  <section class="card card--front" aria-label="Business card, front side">
    <div class="brand-block">
      <div class="brand-mark"></div>
      <div class="brand-name">TalkHarbor</div>
    </div>

    <div class="divider"></div>

    <div class="contact">
      <p class="contact-name"><strong>Arlo</strong> Pennick</p>
      <p class="contact-role">Creative Director</p>
      <p class="contact-address">Calle del Puerto 12,<br>Oficina 3B, 24010, León.</p>
      <ul class="contact-list">
        <li>
          <svg class="contact-icon" viewBox="0 0 16 16" aria-hidden="true">
            <path d="M3.5 1.5l2.5 0 1 3.5-1.6 1.2a8 8 0 0 0 4.4 4.4L11 9l3.5 1v2.5a1.5 1.5 0 0 1-1.5 1.5A11.5 11.5 0 0 1 2 3a1.5 1.5 0 0 1 1.5-1.5z"/>
          </svg>
          +34 900 555 014.
        </li>
        <li>
          <svg class="contact-icon" viewBox="0 0 16 16" aria-hidden="true">
            <path d="M1 3h14v10H1z M1.8 3.8L8 8.6l6.2-4.8" stroke="#fff" stroke-width="1"/>
          </svg>
          hello@talkharbor.co.uk
        </li>
        <li>
          <span class="contact-dot"></span>
          www.talkharbor.co.uk
        </li>
      </ul>
    </div>
  </section>

</main>
</body>
</html>
```